Need Business Card ASAP

We need a business card design for a meeting coming up in a few days. The company name is Harlow Ridge Building and Construction and the logo is attached. Something clean, cool, and contemporary that we can get to a printer right away. Attached is the business card for Volmar Energy, an affiliated company, which we like. Instead of the hawk on the back, you could use the attached "D". We'll also be needing matching letterhead in the near future, so ideas for that are welcome.

```html
<!DOCTYPE html>
<html lang="en">
<head>
<meta charset="utf-8">
<title>Harlow Ridge Building and Construction – Business Card</title>
<link rel="stylesheet" href="https://fonts.googleapis.com/css2?family=Saira+Condensed:wght@600&family=Exo+2:wght@400;600&display=swap">
<style>
  :root {
    --backdrop: #e6e6e4;
    --card: #ffffff;
    --gold: #c6bb88;
    --gold-light: #d6cea4;
    --gold-deep: #a99d69;
    --ink: #231f20;
    --text: #2a2727;
  }
  html, body {
    margin: 0;
    width: 1200px;
    height: 988px;
    overflow: hidden;
    background: var(--backdrop);
  }
  .canvas {
    position: relative;
    width: 1200px;
    height: 988px;
  }
  .card {
    position: absolute;
    left: 270px;
    width: 660px;
    height: 396px;
    background: var(--card);
    box-shadow: 0 2px 6px rgba(0,0,0,0.12);
    overflow: hidden;
  }
  .card--front { top: 70px; }
  .card--back { top: 514px; }

  .ribbon-area {
    position: absolute;
    left: 40px;
    top: 112px;
    width: 572px;
    height: 112px;
    background: linear-gradient(90deg, var(--gold-deep) 0%, var(--gold) 15%, var(--gold-light) 50%, var(--gold) 85%, var(--gold-deep) 100%);
  }
  .ribbon-url {
    position: absolute;
    left: 0;
    top: 148px;
    width: 660px;
    margin: 0;
    text-align: center;
    font-family: "Exo 2", sans-serif;
    font-weight: 600;
    font-size: 15px;
    letter-spacing: 1.5px;
    color: var(--ink);
  }

  .name-band {
    position: absolute;
    left: 0;
    top: 0;
    width: 480px;
    height: 100px;
    background: linear-gradient(90deg, var(--gold) 0%, var(--gold-light) 60%, var(--gold) 100%);
  }
  .fold-area {
    position: absolute;
    left: 480px;
    top: 0;
    width: 156px;
    height: 352px;
    background: linear-gradient(180deg, var(--gold) 0%, var(--gold-deep) 45%, var(--ink) 100%);
  }

  .brand {
    position: absolute;
    width: 140px;
    display: flex;
    flex-direction: column;
    align-items: center;
    font-family: "Exo 2", sans-serif;
    font-weight: 600;
    color: var(--ink);
    text-align: center;
  }
  .card--front .brand { left: 260px; top: 232px; }
  .card--back .brand { left: 250px; top: 172px; }
  .brand__square {
    width: 78px;
    height: 78px;
    background: var(--gold);
    margin-bottom: 10px;
  }
  .brand__name {
    font-size: 19px;
    line-height: 1.05;
  }
  .brand__line {
    margin-top: 4px;
    font-size: 9px;
    letter-spacing: 1px;
    line-height: 1.3;
    text-transform: uppercase;
  }

  .person {
    position: absolute;
    left: 20px;
    top: 14px;
    color: var(--ink);
  }
  .person__name {
    margin: 0;
    font-family: "Saira Condensed", sans-serif;
    font-weight: 600;
    font-size: 46px;
    line-height: 1;
    letter-spacing: 0.5px;
  }
  .person__title {
    margin: 2px 0 0;
    font-family: "Exo 2", sans-serif;
    font-weight: 600;
    font-size: 17px;
    letter-spacing: 1.2px;
  }
  .contacts {
    position: absolute;
    left: 20px;
    top: 244px;
    margin: 0;
    padding: 0;
    list-style: none;
    font-family: "Exo 2", sans-serif;
    font-size: 11px;
    color: var(--text);
  }
  .contacts li {
    display: flex;
    align-items: center;
    height: 23.5px;
  }
  .contacts svg {
    width: 15px;
    height: 15px;
    margin-right: 8px;
    flex: none;
  }
</style>
</head>
<body>
<main class="canvas">

  <section class="card card--front" aria-label="Business card front">
    <div class="ribbon-area" role="img" aria-label="Folded gold and black ribbon illustration"></div>
    <p class="ribbon-url">www.harlowridge-build.com</p>
    <div class="brand">
      <span class="brand__square"></span>
      <span class="brand__name">Harlow Ridge</span>
      <span class="brand__line">Building and<br>Construction</span>
    </div>
  </section>

  <section class="card card--back" aria-label="Business card back">
    <div class="name-band"></div>
    <div class="fold-area" role="img" aria-label="Folded gold and black ribbon illustration"></div>
    <header class="person">
      <h1 class="person__name">EVAN MARSH</h1>
      <p class="person__title">GENERAL MANAGER</p>
    </header>
    <div class="brand">
      <span class="brand__square"></span>
      <span class="brand__name">Harlow Ridge</span>
      <span class="brand__line">Building and<br>Construction</span>
    </div>
    <ul class="contacts">
      <li><svg viewBox="0 0 16 16"><circle cx="8" cy="8" r="7" fill="none" stroke="#231f20" stroke-width="1.3"/><path d="M5.5 4.5l1.5 0 .6 2-1 .8a5 5 0 0 0 2.1 2.1l.8-1 2 .6 0 1.5c-3.5.3-6.3-2.5-6-6z" fill="#231f20"/></svg>014 552 8130</li>
      <li><svg viewBox="0 0 16 16"><circle cx="8" cy="8" r="7" fill="none" stroke="#231f20" stroke-width="1.3"/><rect x="5.8" y="4" width="4.4" height="8" rx="0.8" fill="none" stroke="#231f20" stroke-width="1.1"/></svg>014 552 8131</li>
      <li><svg viewBox="0 0 16 16"><circle cx="8" cy="8" r="7" fill="#231f20"/><rect x="5" y="6.5" width="6" height="4" fill="#fff"/><rect x="6" y="4.5" width="4" height="2" fill="#fff"/></svg>014 552 8132</li>
      <li><svg viewBox="0 0 16 16"><circle cx="8" cy="8" r="7" fill="#231f20"/><rect x="4.5" y="5.5" width="7" height="5" fill="#fff"/><path d="M4.5 5.5l3.5 3 3.5-3" fill="none" stroke="#231f20" stroke-width="0.9"/></svg>evan@harlowridge-build.com</li>
      <li><svg viewBox="0 0 16 16"><circle cx="8" cy="8" r="7" fill="none" stroke="#231f20" stroke-width="1.3"/><circle cx="8" cy="8" r="3.8" fill="none" stroke="#231f20" stroke-width="1"/><path d="M4.2 8h7.6M8 4.2v7.6" stroke="#231f20" stroke-width="0.8"/></svg>www.harlowridge-build.com</li>
      <li><svg viewBox="0 0 16 16"><circle cx="8" cy="8" r="7" fill="none" stroke="#231f20" stroke-width="1.3"/><path d="M8 12.5s-3-3.4-3-5.5a3 3 0 0 1 6 0c0 2.1-3 5.5-3 5.5z" fill="#231f20"/><circle cx="8" cy="7" r="1" fill="#fff"/></svg>42 Kestrel Road, 3rd Floor, Unit 7</li>
    </ul>
  </section>

</main>
</body>
</html>
```